Start-up braucht modernes/hochwertiges Getränkeetikett
Zielgruppe
Wir sind ein modernes, nachhaltiges Start-up, welches eine neue Getränkekategorie auf den Markt bringt. Ein sogenanntes Elektrolyt-Getränk mit dem Namen FLUXO4. Es ist abgefüllt in eine 500 ml Flasche und enthält Magnesium, Kalzium, Kalium, und Natrium. Diese Stoffe (Elektrolyte) dienen der körperlichen Hydrierung. Zu Dehydrierung kann es durch Hitze, Alkohol, Sport oder Krankheit kommen. Krankheit liegt bei uns allerdings nicht im Fokus. In unserer Zielgruppe befinden sich hauptsächlich Personen im Alter von 18 - 29 Jahren.
Die Geschmacksrichtung ist Zitrone-Limette.
Aufgabenstellung
Das Etikett soll:
- MODERN, SCHLICHT und HOCHWERTIG sein, so dass es im Supermarkt hervorsticht
- erkenntlich machen, dass die Stoffe Magnesium, Natrium, Kalzium und Kalium enthalten sind
- sich farblich deutlich von der Farbe des Inhalts (weiß) abheben. (Vorzugsweise mit einem hellen Blau, türkis)
- für unsere junge Zielgruppe ansprechend sein
- ebenfalls auf die Geschmacksrichtung (Zitrone-Limette) hinweisen, und zwar so, dass wenn man eine weitere Geschmacksrichtung auf den Markt bringen möchte, diese leicht angepasst werden kann.
- nicht nach einem Energydrink oder einem typischen Sportgetränk aussehen
- unter dem Namen den Slogan 'Elektrolyt-Getränk' stehen haben
-Das Etikett ist nicht dursichtig sondern besteht aus Papier
Der Name sowie das Logo können selbstverständlich farblich verändert werden. Bei dem Logo können auch größere Änderungen vollzogen werden.
Bitte beachten Sie die unten zu stehenden Regler um sich einen guten Überblick über unsere Vorstellungen zu verschaffen. Die Platzierung des EAN-Code ist für ihr Design irrelevat .
Bei Unklarheiten gerne nachfragen!

```html
<!DOCTYPE html>
<html lang="de">
<head>
<meta charset="utf-8">
<title>FLUXO4 Elektrolyt-Getränk – Etikett</title>
<link rel="stylesheet" href="https://fonts.googleapis.com/css2?family=Montserrat:wght@400;500;700&display=swap">
<style>
  :root {
    --teal: #5cbfb7;
    --teal-deep: #46aaa3;
    --paper: #ffffff;
    --stage: #eef3f3;
    --lemon: #f4dc3a;
    --lime: #8cc84b;
    --leaf: #3f8a3a;
  }
  * { margin: 0; padding: 0; box-sizing: border-box; }
  html, body {
    width: 1200px;
    height: 3009px;
    overflow: hidden;
    background: var(--stage);
    font-family: "Montserrat", sans-serif;
  }
  .label {
    position: absolute;
    left: 50px;
    top: 830px;
    width: 1100px;
    height: 1350px;
    background: var(--teal);
    overflow: hidden;
  }
  .info-column {
    position: absolute;
    left: 0;
    top: 0;
    width: 440px;
    height: 100%;
    background: var(--paper);
    overflow: hidden;
  }
  .mineral-list {
    list-style: none;
    position: absolute;
    left: 70px;
    top: 70px;
    color: var(--teal-deep);
    font-size: 38px;
    font-weight: 500;
    line-height: 1.75;
  }
  .mineral-list li::before {
    content: "+";
    display: inline-block;
    width: 38px;
    font-weight: 700;
  }
  .claim-band {
    position: absolute;
    left: -120px;
    top: 470px;
    width: 700px;
    height: 190px;
    background: var(--teal);
    transform: rotate(-30deg);
    display: flex;
    flex-direction: column;
    justify-content: center;
    align-items: center;
    color: var(--paper);
    font-weight: 700;
    font-size: 54px;
    letter-spacing: 3px;
    line-height: 1.15;
  }
  .variant {
    position: absolute;
    left: 40px;
    bottom: 70px;
    width: 460px;
    transform-origin: left bottom;
    transform: translateY(-0px) rotate(-90deg) translate(0, 100%);
    color: var(--teal-deep);
    font-weight: 500;
    line-height: 1.35;
  }
  .variant-flavour { font-size: 40px; }
  .variant-volume { font-size: 36px; }
  .brand {
    position: absolute;
    left: 440px;
    top: 0;
    width: 660px;
    display: flex;
    flex-direction: column;
    align-items: center;
    padding-top: 110px;
  }
  .brand-circle {
    width: 230px;
    height: 230px;
    border: 5px solid var(--paper);
    border-radius: 50%;
  }
  .brand-name {
    margin-top: 50px;
    color: var(--paper);
    font-size: 130px;
    font-weight: 500;
    letter-spacing: 10px;
  }
  .fruit-visual {
    position: absolute;
    left: 170px;
    top: 760px;
    width: 900px;
    height: 520px;
    border-radius: 46% 46% 40% 40%;
    background: linear-gradient(90deg, var(--lemon) 0%, #f7e88a 38%, var(--leaf) 55%, var(--lime) 75%, #b7e07a 100%);
  }
</style>
</head>
<body>
  <main class="label">
    <section class="info-column">
      <ul class="mineral-list">
        <li>Magnesium</li>
        <li>Natrium</li>
        <li>Kalzium</li>
        <li>Kalium</li>
      </ul>
      <div class="claim-band">
        <span>ELEKTROLYT</span>
        <span>GETRÄNK</span>
      </div>
      <div class="variant">
        <div class="variant-flavour">Zitrone-Limette</div>
        <div class="variant-volume">℮ 500 ml</div>
      </div>
    </section>
    <header class="brand">
      <div class="brand-circle"></div>
      <h1 class="brand-name">FLUXO4</h1>
    </header>
    <div class="fruit-visual" role="img" aria-label="Foto einer halbierten Zitrone und einer halbierten Limette mit grünen Blättern"></div>
  </main>
</body>
</html>
```